New Business Card Design Project

Use the flyer uploaded and website www.brightoakbuilders.com for inspiration.
List Our Services on Backside of business cards
Marcus Delling
Harborline Builders Inc.
Licensed General Contractors
858-471-6093

Contact Information for Business Card

Use the flyer uploaded and website www.brightoakbuilders.com for inspiration. List Our Services on Backside of business cards Marcus Delling Harborline Builders Inc. Licensed General Contractors 858-471-6093

```html
<!DOCTYPE html>
<html lang="en">
<head>
<meta charset="utf-8">
<title>Harborline Builders – Business Cards</title>
<link href="https://fonts.googleapis.com/css2?family=Marcellus&family=PT+Sans:wght@400;700&display=swap" rel="stylesheet">
<style>
  :root {
    --backdrop: #2a2a2c;
    --card: #141414;
    --ink: #f4f4f4;
    --band-text: #141414;
  }
  * { margin: 0; padding: 0; box-sizing: border-box; }
  html, body { width: 900px; height: 1200px; overflow: hidden; }
  body {
    background: var(--backdrop);
    position: relative;
    font-family: "PT Sans", Arial, sans-serif;
    color: var(--ink);
  }
  .card {
    position: absolute;
    left: 134px;
    width: 632px;
    height: 364px;
    background: var(--card);
    box-shadow: 0 6px 18px rgba(0,0,0,0.45);
  }
  .card--services { top: 210px; }
  .card--contact { top: 624px; }

  .brand-name {
    position: absolute;
    font-family: "Marcellus", Georgia, serif;
    font-size: 28px;
    letter-spacing: 1px;
    text-transform: uppercase;
    white-space: nowrap;
    transform: translateX(-50%);
  }
  .card--services .brand-name { left: 187px; top: 164px; }
  .card--contact .brand-name { left: 316px; top: 150px; }

  .services { position: absolute; left: 372px; top: 54px; }
  .services__headline {
    font-weight: 700;
    font-size: 15px;
    line-height: 18px;
    text-transform: uppercase;
  }
  .services__band {
    position: relative;
    margin-top: 3px;
    width: 162px;
    height: 18px;
    background: var(--ink);
    clip-path: polygon(0 0, 100% 0, 92% 100%, 0 100%);
    color: var(--band-text);
    font-weight: 700;
    font-size: 15px;
    line-height: 18px;
    letter-spacing: 0.5px;
    padding-left: 21px;
  }
  .services__list { list-style: none; margin-top: 5px; }
  .services__item {
    display: flex;
    align-items: center;
    height: 22.4px;
    font-size: 14.5px;
    letter-spacing: 0.3px;
  }
  .services__item svg { width: 14px; height: 14px; margin-right: 8px; flex: none; }

  .person {
    position: absolute;
    right: 338px;
    top: 258px;
    text-align: right;
  }
  .person__name {
    font-family: "Marcellus", Georgia, serif;
    font-size: 25px;
    letter-spacing: 1px;
    text-transform: uppercase;
    line-height: 30px;
  }
  .person__title { font-size: 14px; letter-spacing: 0.3px; margin-top: 2px; }

  .divider {
    position: absolute;
    left: 314px;
    top: 250px;
    width: 1.5px;
    height: 74px;
    background: var(--ink);
  }
  .contact { position: absolute; left: 334px; top: 252px; list-style: none; }
  .contact__item {
    display: flex;
    align-items: center;
    height: 25px;
    font-size: 14px;
    letter-spacing: 0.4px;
  }
  .contact__item--phone { letter-spacing: 1.6px; }
  .contact__item svg { width: 14px; height: 14px; margin-right: 6px; flex: none; }
</style>
</head>
<body>

<section class="card card--services">
  <div class="brand-name">Harborline Builders</div>

  <div class="services">
    <p class="services__headline">Our services are<br>100% guaranteed</p>
    <div class="services__band">SPECIALIZING IN:</div>
    <ul class="services__list">
      <li class="services__item"><svg viewBox="0 0 14 14"><rect x="1" y="3" width="10" height="10" fill="none" stroke="#f4f4f4" stroke-width="1.6"/><path d="M3.5 7.5 L6 10 L13 1.5" fill="none" stroke="#f4f4f4" stroke-width="2"/></svg>Remodel: Kitchen &amp; Bath</li>
      <li class="services__item"><svg viewBox="0 0 14 14"><rect x="1" y="3" width="10" height="10" fill="none" stroke="#f4f4f4" stroke-width="1.6"/><path d="M3.5 7.5 L6 10 L13 1.5" fill="none" stroke="#f4f4f4" stroke-width="2"/></svg>Painting: Interior &amp; Exterior</li>
      <li class="services__item"><svg viewBox="0 0 14 14"><rect x="1" y="3" width="10" height="10" fill="none" stroke="#f4f4f4" stroke-width="1.6"/><path d="M3.5 7.5 L6 10 L13 1.5" fill="none" stroke="#f4f4f4" stroke-width="2"/></svg>Flooring: Carpet, Vinyl, Wood</li>
      <li class="services__item"><svg viewBox="0 0 14 14"><rect x="1" y="3" width="10" height="10" fill="none" stroke="#f4f4f4" stroke-width="1.6"/><path d="M3.5 7.5 L6 10 L13 1.5" fill="none" stroke="#f4f4f4" stroke-width="2"/></svg>Window &amp; Door Replacement</li>
      <li class="services__item"><svg viewBox="0 0 14 14"><rect x="1" y="3" width="10" height="10" fill="none" stroke="#f4f4f4" stroke-width="1.6"/><path d="M3.5 7.5 L6 10 L13 1.5" fill="none" stroke="#f4f4f4" stroke-width="2"/></svg>Plumbing: Repairs &amp; Upgrades</li>
      <li class="services__item"><svg viewBox="0 0 14 14"><rect x="1" y="3" width="10" height="10" fill="none" stroke="#f4f4f4" stroke-width="1.6"/><path d="M3.5 7.5 L6 10 L13 1.5" fill="none" stroke="#f4f4f4" stroke-width="2"/></svg>Energy-Efficient Upgrades</li>
      <li class="services__item"><svg viewBox="0 0 14 14"><rect x="1" y="3" width="10" height="10" fill="none" stroke="#f4f4f4" stroke-width="1.6"/><path d="M3.5 7.5 L6 10 L13 1.5" fill="none" stroke="#f4f4f4" stroke-width="2"/></svg>Deck &amp; Patio Construction</li>
      <li class="services__item"><svg viewBox="0 0 14 14"><rect x="1" y="3" width="10" height="10" fill="none" stroke="#f4f4f4" stroke-width="1.6"/><path d="M3.5 7.5 L6 10 L13 1.5" fill="none" stroke="#f4f4f4" stroke-width="2"/></svg>Water &amp; Mold Damage</li>
      <li class="services__item"><svg viewBox="0 0 14 14"><rect x="1" y="3" width="10" height="10" fill="none" stroke="#f4f4f4" stroke-width="1.6"/><path d="M3.5 7.5 L6 10 L13 1.5" fill="none" stroke="#f4f4f4" stroke-width="2"/></svg>Garage Renovation</li>
    </ul>
  </div>
</section>

<section class="card card--contact">
  <div class="brand-name">Harborline Builders</div>

  <div class="person">
    <p class="person__name">Marcus Delling</p>
    <p class="person__title">Business development manager</p>
  </div>

  <div class="divider"></div>

  <ul class="contact">
    <li class="contact__item contact__item--phone"><svg viewBox="0 0 14 14"><path d="M3 1 L5.5 1 L6.5 4 L5 5.3 C5.8 7 7 8.2 8.7 9 L10 7.5 L13 8.5 L13 11 C13 12.2 12 13 10.8 12.9 C5.8 12.4 1.6 8.2 1.1 3.2 C1 2 1.8 1 3 1 Z" fill="#f4f4f4"/></svg>858-471-6093</li>
    <li class="contact__item"><svg viewBox="0 0 14 14"><rect x="0.5" y="2.5" width="13" height="9" fill="#f4f4f4"/><path d="M0.5 2.5 L7 8 L13.5 2.5" fill="none" stroke="#141414" stroke-width="1.2"/></svg>md@brightoakbuilders.com</li>
    <li class="contact__item"><svg viewBox="0 0 14 14"><g fill="none" stroke="#f4f4f4" stroke-width="1.2"><circle cx="7" cy="7" r="6"/><ellipse cx="7" cy="7" rx="2.6" ry="6"/><path d="M1 7 H13 M2 4 H12 M2 10 H12"/></g></svg>www.brightoakbuilders.com</li>
  </ul>
</section>

</body>
</html>
```